RW Framewell Inc Business cards

We need business cards using our existing logo but slightly modified. Right now the logo says RW Loadbearing Masonry. We want to keep the RW part of the design, but replace the Structural Concrete portion with "FRAMEWELL". Please see the attached file.
Ideally this would be a blank template so we can add Different Names, titles, and phone numbers later.
On the one side we want only the logo and on the other side the detail. I'm attaching an example for you to see.
Please reach out with any other questions. Our address and other details will be given out once we find a design we like.

Target Market(s)

Construction Industry

```html
<!DOCTYPE html>
<html lang="en">
<head>
<meta charset="utf-8">
<title>RW Framewell Inc – Business Cards</title>
<link rel="stylesheet" href="https://fonts.googleapis.com/css2?family=Roboto:wght@400;500;700&display=swap">
<style>
  :root {
    --backdrop: #3b3b3d;
    --card-black: #1d1d1f;
    --brand-blue: #2f62a6;
    --accent-grey: #8a8b8d;
    --logo-grey: #6f7072;
    --text-white: #ffffff;
  }
  * { box-sizing: border-box; margin: 0; padding: 0; }
  html, body {
    width: 799px; height: 1200px; overflow: hidden;
    background: var(--backdrop);
    font-family: "Roboto", Arial, sans-serif;
  }
  .sheet {
    width: 799px; height: 1200px;
    display: flex; flex-direction: column;
    align-items: center; justify-content: space-around;
    padding: 60px 0;
  }
  .card {
    position: relative;
    width: 640px; height: 366px;
    border-radius: 4px;
    overflow: hidden;
    box-shadow: 0 18px 40px rgba(0,0,0,0.45);
  }
  .card-front { background: var(--card-black); }
  .brand-name {
    position: absolute;
    color: var(--logo-grey);
    font-weight: 700;
    text-align: left;
    line-height: 1;
  }
  .card-front .brand-name { left: 150px; top: 108px; }
  .brand-initials { display: block; font-size: 118px; letter-spacing: 4px; }
  .brand-word { display: block; font-size: 38px; letter-spacing: 9px; margin-top: 10px; }

  .card-back { background: var(--brand-blue); }
  .back-shapes { position: absolute; inset: 0; }
  .card-back .brand-name { left: 40px; top: 112px; }
  .card-back .brand-initials { font-size: 84px; letter-spacing: 3px; }
  .card-back .brand-word { font-size: 23px; letter-spacing: 5px; margin-top: 8px; }

  .contact {
    position: absolute; left: 360px; top: 92px;
    color: var(--text-white);
  }
  .contact-name { font-size: 27px; font-weight: 700; }
  .contact-title { font-size: 16px; margin-top: 2px; margin-bottom: 18px; }
  .contact-line {
    display: flex; align-items: center; gap: 10px;
    font-size: 17px; margin-bottom: 8px;
  }
  .contact-line svg { width: 16px; height: 16px; flex: none; }
  .contact-address { font-size: 17px; line-height: 1.35; margin-top: 4px; }
</style>
</head>
<body>
<main class="sheet">
  <section class="card card-front" aria-label="Business card front">
    <div class="brand-name">
      <span class="brand-initials">RW</span>
      <span class="brand-word">FRAMEWELL</span>
    </div>
  </section>

  <section class="card card-back" aria-label="Business card back">
    <svg class="back-shapes" viewBox="0 0 640 366" preserveAspectRatio="none" aria-hidden="true">
      <path d="M0 0 H314 C349 110 334 270 226 366 H0 Z" fill="var(--accent-grey)"/>
      <path d="M0 0 H300 C335 110 320 270 210 366 H0 Z" fill="var(--card-black)"/>
    </svg>
    <div class="brand-name">
      <span class="brand-initials">RW</span>
      <span class="brand-word">FRAMEWELL</span>
    </div>
    <div class="contact">
      <p class="contact-name">Daniel Marsh</p>
      <p class="contact-title">Managing Director</p>
      <p class="contact-line">
        <svg viewBox="0 0 16 16"><path d="M3 2h3l1.5 3.5-2 1.2a8 8 0 0 0 3.8 3.8l1.2-2L14 10v3a1 1 0 0 1-1 1A11 11 0 0 1 2 3a1 1 0 0 1 1-1z" fill="#fff"/></svg>
        555-010-2040
      </p>
      <p class="contact-line">
        <svg viewBox="0 0 16 16"><rect x="1" y="3" width="14" height="10" fill="#fff"/><path d="M1 3l7 6 7-6" fill="none" stroke="var(--brand-blue)" stroke-width="1.4"/></svg>
        dan@framewellbuild.com
      </p>
      <p class="contact-line">
        <svg viewBox="0 0 16 16"><circle cx="8" cy="8" r="6.5" fill="none" stroke="#fff" stroke-width="1.4"/><ellipse cx="8" cy="8" rx="2.8" ry="6.5" fill="none" stroke="#fff" stroke-width="1.2"/><path d="M1.5 8h13" stroke="#fff" stroke-width="1.2"/></svg>
        www.framewellbuild.com
      </p>
      <p class="contact-address">78 Ridgeline Rd., Millbrook,<br>California, US 95012</p>
    </div>
  </section>
</main>
</body>
</html>
```